Need a stunning home page for Car rental company

For a client, I need a slick and sumber home page design. It is a small, local car rental company, with a handful of cars available for rent.
Selling points: affordable lease, availability, always clean cars
The design should be:
- flat and modern
- no, or very few animations/sliders
- CTA: booking form for renting a car.
- 3 featured cars with images and facts (see website) with button to read more about the car.
- fullscreen background video can be an option
- main colour: #efba01
The site is under construction here:
http://solvikutleie.hammerlia.no/
Delivery requirements:
I need a layered & well organised PSD file delivered.

```html
<!DOCTYPE html>
<html lang="no">
<head>
<meta charset="utf-8">
<title>Solvik Utleie – Bilutleie</title>
<link href="https://fonts.googleapis.com/css2?family=Open+Sans:wght@400;600;700&family=Ubuntu:wght@400;500&display=swap" rel="stylesheet">
<style>
:root{
  --brand:#efba01;
  --brand-dark:#d9a800;
  --grey-nav:#8c8c8c;
  --ink:#333;
  --muted:#666;
  --card:#e8e8e8;
  --footer:#111;
  --white:#fff;
  --submit:#7a7a7a;
}
*{box-sizing:border-box;margin:0;padding:0}
html,body{width:747px;height:1200px;overflow:hidden}
body{position:relative;background:var(--white);font-family:"Open Sans",sans-serif;color:var(--ink)}
.abs{position:absolute}

.top-line{left:0;top:0;width:747px;height:3px;background:var(--brand)}
.top-line .grey{position:absolute;left:0;top:0;width:570px;height:3px;background:#888}
.lang{left:570px;top:0;width:110px;height:22px;background:var(--brand);border-radius:0 0 14px 14px;font-size:7px;color:var(--ink);display:flex;align-items:center;justify-content:center;gap:4px;font-weight:600}
.lang .flag{width:11px;height:7px;background:#c33;border:1px solid #fff}
.logo{left:62px;top:22px;font-family:"Open Sans",sans-serif;font-weight:700;font-size:21px;letter-spacing:1px;color:#555;display:flex;align-items:center;gap:6px}
.logo .mark{width:10px;height:10px;background:var(--brand)}
.contact{right:62px;top:34px;font-size:8px;font-weight:600;display:flex;align-items:center;gap:6px}

.nav{left:0;top:62px;width:747px;height:45px;background:var(--brand);border-bottom:2px solid #ccc}
.nav ul{list-style:none;display:flex;height:100%;margin-left:62px}
.nav li{font-size:8px;font-weight:600;color:var(--ink);display:flex;align-items:center;padding:0 20px;height:100%}
.nav li.active{background:var(--grey-nav);color:#fff;padding:0 31px}

.hero{left:0;top:108px;width:747px;height:297px;background:linear-gradient(160deg,#3d4238 0%,#6b705e 30%,#b9bdb9 55%,#8b8f8c 80%,#6f6f6f 100%)}
.hero-arrow{width:19px;height:19px;border-radius:50%;background:#fff;display:flex;align-items:center;justify-content:center}
.dots{left:339px;top:389px;display:flex;gap:3px}
.dots span{width:7px;height:7px;border-radius:50%;background:#fff;border:1px solid #666}
.dots span.on{background:var(--brand)}

.booking{left:503px;top:325px;width:180px;height:238px;background:#fff;box-shadow:0 6px 10px rgba(0,0,0,.18)}
.booking h3{background:var(--brand);color:#fff;font-family:"Ubuntu",sans-serif;font-weight:400;font-size:11px;height:30px;padding:8px 10px}
.radios{display:flex;gap:10px;font-size:7px;padding:10px 9px 5px;align-items:center}
.radios span{display:flex;align-items:center;gap:4px}
.radios i{width:8px;height:8px;border-radius:50%;display:inline-block}
.field{margin:6px 9px 0;height:21px;border:1px solid #ccc;font-size:7px;color:#777;display:flex;align-items:center;justify-content:space-between;padding:0 6px;box-shadow:inset 0 1px 2px rgba(0,0,0,.08)}
.submit{position:absolute;left:9px;top:199px;width:157px;height:20px;background:var(--submit);color:#fff;font-size:7px;display:flex;align-items:center;justify-content:center}

.h2{font-family:"Ubuntu",sans-serif;color:var(--brand);font-weight:500}
.welcome-title{left:63px;top:418px;font-size:18px}
.welcome-text{left:62px;top:446px;width:425px;font-size:6.6px;line-height:15px;color:var(--muted)}
.offers-title{left:64px;top:574px;font-size:18px}

.card{top:608px;width:198px;height:327px;background:var(--card);border-top:2px solid var(--brand)}
.card .photo{height:132px}
.card h4{font-family:"Ubuntu",sans-serif;font-weight:500;font-size:10px;margin:12px 7px 11px}
.card table{width:184px;margin:0 7px;border-collapse:collapse;font-size:7px;color:var(--muted)}
.card td{height:15px}
.card td:last-child{width:40px}
.card tr.price td{font-weight:600;color:var(--ink);height:20px}
.card tr.price td:last-child{color:var(--brand)}
.card .more{position:absolute;left:0;bottom:0;width:100%;height:26px;background:var(--brand);font-size:8px;display:flex;align-items:center;justify-content:center}

.gallery-title{left:62px;top:958px;font-size:18px}
.gallery-nav{left:662px;top:958px}
.shot{top:993px;width:193px;height:104px}

.footer{left:0;top:1120px;width:747px;height:80px;background:var(--footer);color:#fff}
.footer .links{position:absolute;left:63px;top:30px;font-size:7px}
.footer .copy{position:absolute;left:63px;top:45px;font-size:7px}
.social{position:absolute;left:605px;top:27px;display:flex;gap:6px}
.social span{width:23px;height:23px;border-radius:50%;background:#ddd}
</style>
</head>
<body>
<div class="abs top-line"><div class="grey"></div></div>
<div class="abs lang"><span class="flag"></span>English ▾</div>
<div class="abs logo"><span class="mark"></span>SOLVIK UTLEIE</div>
<div class="abs contact">
  <svg width="14" height="11" viewBox="0 0 14 11"><path d="M1 4C1 1 13 1 13 4v1h-3V3.5H4V5H1z" fill="#333"/><rect x="3" y="5" width="8" height="5" rx="1" fill="#333"/></svg>
  Spørsmål? Ring oss 91234567
</div>

<nav class="abs nav"><ul>
  <li class="active">HJEM</li><li>BILPARKEN VÅR</li><li>TJENESTER</li><li>KONTAKT OSS</li><li>BLOG</li><li>PAGE TEMPLATES</li><li>ABOUT US</li>
</ul></nav>

<div class="abs hero" role="img" aria-label="Video backdrop of a dark blue convertible driving along a lakeside road"></div>
<div class="abs hero-arrow" style="left:39px;top:218px"><svg width="8" height="8" viewBox="0 0 8 8"><path d="M5.5 1L2.5 4l3 3" stroke="#333" stroke-width="1.6" fill="none"/></svg></div>
<div class="abs hero-arrow" style="left:707px;top:218px"><svg width="8" height="8" viewBox="0 0 8 8"><path d="M2.5 1l3 3-3 3" stroke="#333" stroke-width="1.6" fill="none"/></svg></div>
<svg class="abs" style="left:342px;top:215px" width="44" height="44" viewBox="0 0 44 44"><circle cx="22" cy="22" r="19" stroke="#fff" stroke-width="3.5" fill="none"/><path d="M17 13l13 9-13 9z" fill="#fff"/></svg>
<div class="abs dots"><span class="on"></span><span></span><span></span></div>

<form class="abs booking">
  <h3>Booking Form</h3>
  <div class="radios">
    <span><i style="border:2px solid #f07b1a;background:#f7a04f"></i>Rent</span>
    <span><i style="background:#2e3a5a"></i>Sale</span>
  </div>
  <div class="field">Vehicle Type<span>⬍</span></div>
  <div class="field" style="margin-top:11px">Model<span>⬍</span></div>
  <div class="field" style="margin-top:12px">Brand<span>⬍</span></div>
  <div class="field" style="margin-top:10px">Year From<span>⬍</span></div>
  <div class="submit">Submit</div>
</form>

<h1 class="abs h2 welcome-title">Welcome To Solvik Utleie</h1>
<p class="abs welcome-text">Lorem ipsum dolor sit amet, consectetur adipiscing elit. Donec sit amet turpis erat. Aenean hendrerit fermentum aliquet. Nunc id nunc sapien. Suspendisse euismod dui lorem, nec fringilla arcu bibendum ac. Sed tristique augue tincidunt libero egestas, eu accumsan erat lacinia. Lorem ipsum dolor sit amet, consectetur adipiscing elit. Donec sit amet turpis erat. Aenean hendrerit fermentum aliquet. Nunc id nunc sapien. Suspendisse euismod dui lorem, nec fringilla arcu bibendum ac. Lorem ipsum dolor sit amet, consectetur adipiscing elit. Donec sit amet turpis erat. Aenean hendrerit fermentum aliquet. Nunc id nunc sapien. Suspendisse euismod dui lorem, nec fringilla arcu bibendum ac.</p>

<h2 class="abs h2 offers-title">Våre leietilbud</h2>

<article class="abs card" style="left:62px">
  <div class="photo" role="img" aria-label="Red hatchback on a mountain road beside a cliff" style="background:linear-gradient(180deg,#a89c88,#6d6658 60%,#8a8a86)"></div>
  <h4>Varebilen</h4>
  <table>
    <tr class="price"><td>Pris per døgn</td><td>kr 600</td></tr>
    <tr><td>Biltype</td><td>Varebil</td></tr><tr><td>Maks. pers.</td><td>2</td></tr><tr><td>Ant. dører</td><td>5</td></tr><tr><td>Min. sjåføralder</td><td>21</td></tr><tr><td>Girtype</td><td>Manuell</td></tr><tr><td>Klimaanlegg?</td><td>Ja</td></tr><tr><td>Ubegrenset km?</td><td>Nei</td></tr>
  </table>
  <div class="more">Read More</div>
</article>
<article class="abs card" style="left:275px">
  <div class="photo" role="img" aria-label="White van parked on gravel" style="background:linear-gradient(180deg,#d8d8d8,#eeeeee 50%,#7d7a72)"></div>
  <h4>Varebilen</h4>
  <table>
    <tr class="price"><td>Pris per døgn</td><td>kr 600</td></tr>
    <tr><td>Biltype</td><td>Varebil</td></tr><tr><td>Maks. pers.</td><td>2</td></tr><tr><td>Ant. dører</td><td>5</td></tr><tr><td>Min. sjåføralder</td><td>21</td></tr><tr><td>Girtype</td><td>Manuell</td></tr><tr><td>Klimaanlegg?</td><td>Ja</td></tr><tr><td>Ubegrenset km?</td><td>Nei</td></tr>
  </table>
  <div class="more">Read More</div>
</article>
<article class="abs card" style="left:487px">
  <div class="photo" role="img" aria-label="Red sports coupe speeding on a road" style="background:linear-gradient(180deg,#4d6b3d,#9a9d96 45%,#c9473c 62%,#777 80%)"></div>
  <h4>Varebilen</h4>
  <table>
    <tr class="price"><td>Pris per døgn</td><td>kr 600</td></tr>
    <tr><td>Biltype</td><td>Varebil</td></tr><tr><td>Maks. pers.</td><td>2</td></tr><tr><td>Ant. dører</td><td>5</td></tr><tr><td>Min. sjåføralder</td><td>21</td></tr><tr><td>Girtype</td><td>Manuell</td></tr><tr><td>Klimaanlegg?</td><td>Ja</td></tr><tr><td>Ubegrenset km?</td><td>Nei</td></tr>
  </table>
  <div class="more">Read More</div>
</article>

<h2 class="abs h2 gallery-title">Gallery</h2>
<svg class="abs gallery-nav" width="22" height="12" viewBox="0 0 22 12"><path d="M7 1L2 6l5 5M15 1l5 5-5 5" stroke="#555" stroke-width="2.5" fill="none"/></svg>
<div class="abs shot" style="left:62px;background:radial-gradient(ellipse at 50% 55%,#d0212b 0%,#7a1016 40%,#0b0b0b 75%)" role="img" aria-label="Red sports car on black background"></div>
<div class="abs shot" style="left:277px;background:linear-gradient(170deg,#5a4a3a,#e2c21a 45%,#f2d52a 60%,#6a6a6a)" role="img" aria-label="Yellow muscle car in motion"></div>
<div class="abs shot" style="left:492px;background:linear-gradient(180deg,#3f78c4,#c9dcf0 50%,#7d8a6a 62%,#8a8a8a)" role="img" aria-label="Silver car on an open highway under blue sky"></div>

<footer class="abs footer">
  <div class="links">Home &nbsp;| &nbsp;About us &nbsp;| &nbsp;Counselling &nbsp;| &nbsp;Workshop &nbsp;| &nbsp;Contact us</div>
  <div class="copy">Content copyright 2014. Nordlys Web. All rights reserved.</div>
  <div class="social"><span></span><span></span><span></span></div>
</footer>
</body>
</html>
```